Business Card Design for a Personal Trainer

I need a business card design for my job as a personal trainer. It should have a unique, modern and exclusive design. On the front there should be only my logo with my name and my job. 0162/3819204 Tobias Lendhart Wiesengrundweg 14 80417 Munich Germany The most important contact information is the web adress. it can be bigger than the rest, but its not necessary. The card should be 8,5cmx5,5cm big. Font: Roboto. Colors: black, white, gray, 56c1ff.

```html
<!DOCTYPE html>
<html lang="de">
<head>
<meta charset="utf-8">
<title>Tobias Lendhart – Personal Trainer Business Card</title>
<link href="https://fonts.googleapis.com/css2?family=Roboto:wght@400&family=Work+Sans:wght@400;500&display=swap" rel="stylesheet">
<style>
  :root {
    --page-bg: #dcdcdc;
    --card-white: #ffffff;
    --card-black: #050505;
    --ink: #1e1c1d;
    --ink-soft: #2a2a2a;
    --photo-light: #5a5a5a;
    --photo-dark: #141414;
  }
  * { margin: 0; padding: 0; box-sizing: border-box; }
  html, body {
    width: 1200px; height: 897px; overflow: hidden;
    background: var(--page-bg);
  }
  .canvas { position: relative; width: 1200px; height: 897px; }

  .card {
    position: absolute; left: 329px; width: 543px; height: 310px;
    overflow: hidden;
  }
  .card--front { top: 108px; background: var(--card-white); color: var(--ink); }
  .card--back { top: 479px; background: var(--card-black); color: var(--card-white); }

  .brand-name {
    position: absolute; font-family: "Roboto", sans-serif; font-weight: 400;
    white-space: nowrap; line-height: 1;
  }
  .brand-role {
    position: absolute; font-family: "Roboto", sans-serif; font-weight: 400;
    letter-spacing: 3px; white-space: nowrap; line-height: 1;
  }
  .card--front .brand-name { right: 20px; top: 88px; font-size: 21px; }
  .card--front .brand-role { right: 30px; top: 113px; font-size: 9px; }

  .holder-name {
    position: absolute; left: 22px; top: 163px;
    font-family: "Work Sans", sans-serif; font-weight: 500;
    font-size: 17px; letter-spacing: 0.8px; line-height: 1;
  }
  .holder-role {
    position: absolute; left: 22px; top: 187px;
    font-family: "Work Sans", sans-serif; font-size: 13px; line-height: 1;
  }
  .divider {
    position: absolute; left: 22px; right: 20px; top: 209px;
    height: 2px; background: var(--ink);
  }
  .contact-list {
    position: absolute; left: 22px; top: 232px; list-style: none;
    font-family: "Work Sans", sans-serif; font-size: 14px; color: var(--ink-soft);
  }
  .contact-list li { display: flex; align-items: center; height: 19px; }
  .contact-list svg { width: 9px; height: 9px; margin-right: 6px; }
  .address {
    position: absolute; right: 20px; top: 251px; text-align: right;
    font-family: "Work Sans", sans-serif; font-size: 14px; color: var(--ink-soft);
    font-style: normal; line-height: 19px;
  }
  .footer-band {
    position: absolute; left: 0; right: 0; bottom: 0; height: 6px;
    background: var(--ink);
  }

  .portrait {
    position: absolute; left: 0; top: 0; width: 254px; height: 100%;
    background: radial-gradient(ellipse at 45% 55%, var(--photo-light) 0%, var(--photo-dark) 75%);
  }
  .card--back .brand-name { left: 399px; transform: translateX(-50%); top: 174px; font-size: 24px; }
  .card--back .brand-role { left: 399px; transform: translateX(-50%); top: 199px; font-size: 10px; }
</style>
</head>
<body>
<main class="canvas">
  <section class="card card--front" aria-label="Card front">
    <div class="brand-name">TOBIAS LENDHART</div>
    <div class="brand-role">PERSONAL TRAINER</div>

    <div class="holder-name">TOBIAS LENDHART</div>
    <div class="holder-role">Personal Trainer</div>
    <div class="divider"></div>

    <ul class="contact-list">
      <li>
        <svg viewBox="0 0 10 10" aria-hidden="true"><path d="M2 1 L4 1 L4.5 3 L3.3 4 Q4.5 6.5 6 7 L7 5.7 L9 6.2 L9 8.5 Q4.5 9 1.5 4 Q1 2 2 1Z" fill="currentColor"/></svg>
        0162/3819204
      </li>
      <li>
        <svg viewBox="0 0 10 10" aria-hidden="true"><rect x="0.8" y="2" width="8.4" height="6" fill="none" stroke="currentColor" stroke-width="1.2"/><path d="M1 2.3 L5 5.4 L9 2.3" fill="none" stroke="currentColor" stroke-width="1.1"/></svg>
        t.lendhart@mailpost.de
      </li>
      <li>
        <svg viewBox="0 0 10 10" aria-hidden="true"><circle cx="5" cy="5" r="4" fill="none" stroke="currentColor" stroke-width="1"/><ellipse cx="5" cy="5" rx="1.8" ry="4" fill="none" stroke="currentColor" stroke-width="0.9"/><path d="M1 5 H9" stroke="currentColor" stroke-width="0.9"/></svg>
        www.tobiaslendhart.de
      </li>
    </ul>

    <address class="address">Wiesengrundweg 14<br>80417 München</address>
    <div class="footer-band"></div>
  </section>

  <section class="card card--back" aria-label="Card back">
    <div class="portrait" role="img" aria-label="Black and white portrait of the trainer with arms crossed"></div>
    <div class="brand-name">TOBIAS LENDHART</div>
    <div class="brand-role">PERSONAL TRAINER</div>
  </section>
</main>
</body>
</html>
```